Kelo Wave Mint Business cards

Logo, tag line and photo on card
Agent Name
Title
Address
Phone number
Email
Website
Make logo on one side large by rotating  to portrait format.  Keep the background of the logo white.

Contact Information for Business Card
Slogan; Making Every Wave Count

```html
<!DOCTYPE html>
<html lang="en">
<head>
<meta charset="utf-8">
<title>Kelo Wave Mint Business Cards</title>
<link href="https://fonts.googleapis.com/css2?family=Open+Sans:wght@400;600;700;800&display=swap" rel="stylesheet">
<style>
  :root {
    --stage: #222222;
    --card: #ffffff;
    --navy: #1f2f6b;
    --red: #c62127;
    --ink: #1a1a1a;
    --photo-light: #e9e9ea;
    --photo-mid: #9a9a9c;
    --photo-dark: #4a4a4d;
  }
  * { box-sizing: border-box; margin: 0; padding: 0; }
  html, body {
    width: 1200px; height: 711px; overflow: hidden;
    background: var(--stage);
    font-family: "Open Sans", Arial, sans-serif;
  }
  .sheet {
    width: 1200px; height: 711px;
    display: flex; align-items: center; justify-content: center; gap: 50px;
  }
  .card {
    position: relative;
    width: 540px; height: 309px;
    background: var(--card);
    border-radius: 22px;
    border-bottom: 4px solid var(--red);
    overflow: hidden;
  }

  /* Front */
  .card-front {
    display: flex; flex-direction: column; align-items: center; justify-content: center;
  }
  .brand-stack {
    display: flex; flex-direction: column; align-items: center;
    color: var(--navy); font-weight: 800; font-size: 58px; line-height: 0.95;
    letter-spacing: -1px;
  }
  .tagline {
    margin-top: 22px;
    color: var(--red); font-weight: 600; font-size: 15px; letter-spacing: 0.3px;
  }

  /* Back */
  .brand-small {
    position: absolute; left: 30px; top: 28px;
    color: var(--navy); font-weight: 800; font-size: 28px; line-height: 0.95;
    letter-spacing: -0.5px;
  }
  .agent {
    position: absolute; left: 0; top: 150px;
    padding-left: 32px;
  }
  .agent-bar {
    position: absolute; left: 0; top: 4px;
    width: 14px; height: 48px; background: var(--red);
  }
  .agent-name { font-weight: 700; font-size: 24px; line-height: 1.1; }
  .agent-name .first { color: var(--red); }
  .agent-name .last { color: var(--navy); }
  .agent-title { font-weight: 600; font-size: 12.5px; color: var(--ink); margin-top: 2px; }
  .address {
    position: absolute; left: 46px; top: 212px;
    font-size: 12.5px; line-height: 1.35; color: var(--ink);
  }
  .contact-list {
    position: absolute; left: 46px; top: 252px;
    list-style: none; font-size: 12.5px; color: var(--ink);
  }
  .contact-list li { display: flex; align-items: center; gap: 8px; height: 17px; }
  .contact-list svg { width: 12px; height: 12px; flex: none; }
  .portrait {
    position: absolute; right: 0; top: 40px;
    width: 245px; height: 265px;
    background: radial-gradient(ellipse at 45% 35%, var(--photo-light) 0%, var(--photo-mid) 45%, var(--photo-dark) 100%);
    border-top-left-radius: 120px;
  }
</style>
</head>
<body>
<main class="sheet">
  <section class="card card-front">
    <div class="brand-stack">
      <span>Kelo</span>
      <span>Wave</span>
      <span>Mint</span>
    </div>
    <p class="tagline">Making Every Wave Count</p>
  </section>

  <section class="card card-back">
    <div class="brand-small">Kelo<br>Wave<br>Mint</div>

    <div class="agent">
      <span class="agent-bar"></span>
      <p class="agent-name"><span class="first">Maren</span> <span class="last">Holcroft</span></p>
      <p class="agent-title">Managing Director</p>
    </div>

    <p class="address">4712 Cedar Hollow Dr. Suite<br>110 Fort Worth, TX 76109</p>

    <ul class="contact-list">
      <li>
        <svg viewBox="0 0 12 12" aria-hidden="true"><path fill="#c62127" d="M2.5 1h2l1 2.8-1.3 1a6 6 0 0 0 2.9 2.9l1-1.3L11 7.5v2c0 .8-.7 1.5-1.5 1.5A8.5 8.5 0 0 1 1 2.5C1 1.7 1.7 1 2.5 1z"/></svg>
        (817) 555-0142
      </li>
      <li>
        <svg viewBox="0 0 12 12" aria-hidden="true"><rect x="1" y="2.5" width="10" height="7" rx="1" fill="#c62127"/><path d="M1.5 3l4.5 3.5L10.5 3" stroke="#fff" stroke-width="1" fill="none"/></svg>
        info@kelowavemint.com
      </li>
      <li>
        <svg viewBox="0 0 12 12" aria-hidden="true"><circle cx="6" cy="6" r="5" fill="#c62127"/><path d="M1 6h10M6 1c-2.5 2.8-2.5 7.2 0 10M6 1c2.5 2.8 2.5 7.2 0 10" stroke="#fff" stroke-width="0.8" fill="none"/></svg>
        www.kelowavemint.com
      </li>
    </ul>

    <div class="portrait" role="img" aria-label="Portrait photo of the agent, smiling, in a patterned shirt on a white background"></div>
  </section>
</main>
</body>
</html>
```